Meridale Bed Company Needs Business Card

Looking for a very nice looking business card. Creative but not extravagant. We sell beds and pillows across the U.S. and need something professional but catchy. I have attached the logo.

Name : Devin Holt
Title : President
Phone : (800) 471-2960
Email: sleep@quilmora.com
Website: www.quilmora.com

Can be single-sided or double-sided
horizontal or vertical

Can use Blues/Greys

Target Market(s)

Mass Market

Industry/Entity Type

Retail

Contact Information for Business Card

Name : Devin Holt
Title : President
Phone : (800) 471-2960
Email: sleep@quilmora.com
Website: www.quilmora.com

Requirements
Must have
• Clean, Modern, Smooth
• Can use Blues/Greys
• On the other side without the information - have something simple like www.quilmora.com or our logo
Nice to have
• Surprise me
Should not have
• Nothing crazy, nothing cluttered

```html
<!DOCTYPE html>
<html lang="en">
<head>
<meta charset="utf-8">
<title>Quilmora Business Card</title>
<link href="https://fonts.googleapis.com/css2?family=Lato:ital,wght@0,300;0,400;0,700;1,400&display=swap" rel="stylesheet">
<style>
  :root {
    --page-bg: #e6e9ec;
    --card-light: #f3f4f6;
    --card-edge: #c5cad0;
    --brand-blue: #1f6fb5;
    --panel-top: #2b86cc;
    --panel-bottom: #135ea6;
    --logo-blue: #4b7ea6;
    --text-white: #ffffff;
    --text-soft: #e3eef8;
    --web-text: #3a5670;
  }
  * { margin: 0; padding: 0; box-sizing: border-box; }
  html, body {
    width: 1200px;
    height: 970px;
    overflow: hidden;
    background: var(--page-bg);
    font-family: "Lato", Arial, sans-serif;
  }
  .business-card {
    position: absolute;
    left: 100px;
    top: 185px;
    width: 1000px;
    height: 598px;
    background: var(--card-light);
    border: 1px solid var(--card-edge);
    overflow: hidden;
  }
  .brand-name {
    position: absolute;
    left: 53px;
    top: 256px;
    font-family: "Lato", Arial, sans-serif;
    font-weight: 300;
    font-size: 86px;
    line-height: 1;
    letter-spacing: 1px;
    color: var(--logo-blue);
  }
  .divider-line {
    position: absolute;
    top: 0;
    width: 5px;
    height: 100%;
    background: var(--brand-blue);
  }
  .divider-line.first { left: 487px; }
  .divider-line.second { left: 499px; }
  .info-panel {
    position: absolute;
    left: 510px;
    top: 0;
    right: 0;
    bottom: 0;
    background: linear-gradient(160deg, var(--panel-top), var(--panel-bottom));
  }
  .person-name {
    position: absolute;
    left: 73px;
    top: 163px;
    font-weight: 700;
    font-size: 35px;
    color: var(--text-white);
  }
  .person-title {
    position: absolute;
    left: 73px;
    top: 206px;
    font-style: italic;
    font-size: 25px;
    color: var(--text-soft);
  }
  .contact-line {
    position: absolute;
    left: 73px;
    display: flex;
    align-items: center;
    gap: 12px;
    font-size: 27px;
    color: var(--text-white);
  }
  .contact-line.phone { top: 275px; }
  .contact-line.email { top: 326px; }
  .contact-line svg { width: 30px; height: 26px; flex: none; }
  .website {
    position: absolute;
    left: 75px;
    top: 384px;
    font-weight: 700;
    font-size: 24px;
    letter-spacing: 5px;
    color: var(--web-text);
    opacity: 0.85;
  }
</style>
</head>
<body>
  <div class="business-card">
    <div class="brand-name">quilmora</div>
    <div class="divider-line first"></div>
    <div class="divider-line second"></div>
    <div class="info-panel">
      <div class="person-name">Devin Holt</div>
      <div class="person-title">President</div>
      <div class="contact-line phone">
        <svg viewBox="0 0 30 26" aria-hidden="true">
          <path d="M2 9 Q15 0 28 9 L28 12 L22 12 L21 9 Q15 7 9 9 L8 12 L2 12 Z" fill="#fff"/>
          <path d="M7 13 L23 13 L27 24 L3 24 Z" fill="#fff"/>
          <circle cx="15" cy="18.5" r="3.2" fill="#1f6fb5"/>
        </svg>
        <span>(800) 471-2960</span>
      </div>
      <div class="contact-line email">
        <svg viewBox="0 0 30 26" aria-hidden="true">
          <rect x="2" y="4" width="26" height="18" fill="none" stroke="#fff" stroke-width="2.2"/>
          <path d="M2 4 L15 15 L28 4 M2 22 L11 12 M28 22 L19 12" fill="none" stroke="#fff" stroke-width="2"/>
        </svg>
        <span>sleep@quilmora.com</span>
      </div>
      <div class="website">www.quilmora.com</div>
    </div>
  </div>
</body>
</html>
```